Wordpress Template Design using existing Logo and Colors

We are wanting a wordpress theme designing for our b2b marketing consultancy business. A comprehesive and elagant design to our current site www.plovtrix.com would be good.

Industry/Entity Type

Marketing

Font styles to use
Sans Serif

```html
<!DOCTYPE html>
<html lang="en">
<head>
<meta charset="utf-8">
<title>Plovtrix – B2B Marketing Consultancy</title>
<link rel="stylesheet" href="https://fonts.googleapis.com/css2?family=Montserrat:wght@400;600;700&family=Open+Sans:wght@400;600;700&family=Raleway:wght@500;600&display=swap">
<style>
:root{
  --red:#ec1c24;
  --dark:#3d4150;
  --darker:#343744;
  --navy:#1f2a44;
  --text:#555a63;
  --muted:#8a8e96;
  --light:#f0f0f0;
  --white:#fff;
  --black:#111;
}
*{box-sizing:border-box;margin:0;padding:0}
html,body{width:1200px;height:3442px;overflow:hidden}
body{position:relative;font-family:"Open Sans",sans-serif;color:var(--text);background:var(--white)}
.abs{position:absolute}
h1,h2,h3,h4{font-family:"Montserrat",sans-serif}

/* hero */
.hero{left:0;top:0;width:1200px;height:672px;background:linear-gradient(100deg,#d8d6d2 0%,#bfb9b1 40%,#7a6f66 70%,#4b4d55 100%)}
.topbar{left:0;top:0;width:1200px;height:46px;background:rgba(40,43,54,.85);color:#fff;font-size:13px}
.topbar .addr{left:172px;top:14px}
.topbar .pin{left:160px;top:14px}
.social{display:flex;gap:14px;left:895px;top:12px}
.social span{width:20px;height:20px;border-radius:50%;background:rgba(255,255,255,.85)}
.social span.on{background:#2a9fd6}
.lang{left:1005px;top:13px}
.header{left:160px;top:46px;width:877px;height:85px;background:var(--white)}
.brand{left:20px;top:24px;display:flex;align-items:center;gap:10px;font-family:"Montserrat",sans-serif;font-weight:700;font-size:32px;color:var(--red);letter-spacing:1px}
.brand i{width:14px;height:14px;background:var(--navy)}
.hcontact{display:flex;gap:12px;align-items:center;font-size:12px;color:var(--text)}
.hcontact .ic{width:40px;height:40px;border:1px solid #ddd;border-radius:3px;display:flex;align-items:center;justify-content:center}
.hcontact b{display:block;color:#222;font-weight:600;font-size:12px}
.consult{left:727px;top:22px;width:141px;height:40px;background:var(--red);color:#fff;font:700 12px "Montserrat",sans-serif;display:flex;align-items:center;justify-content:center}
.nav{left:160px;top:131px;width:877px;height:41px;background:var(--dark);display:flex;align-items:center;font:600 13px "Montserrat",sans-serif;color:#fff}
.nav .home{width:41px;height:41px;background:var(--red);display:flex;align-items:center;justify-content:center;margin-right:16px}
.nav a{margin-right:23px}
.hero h1{left:0;top:350px;width:1200px;text-align:center;color:#fff;font-size:37px;font-weight:600;text-shadow:0 2px 6px rgba(0,0,0,.4)}
.hero .sub{left:300px;top:417px;width:600px;text-align:center;color:#fff;font-size:14px;line-height:26px}
.btn{display:flex;align-items:center;justify-content:center;color:#fff;font:700 11px "Montserrat",sans-serif}
.b1{left:483px;top:482px;width:117px;height:32px;background:var(--red)}
.b2{left:607px;top:482px;width:120px;height:32px;background:var(--dark)}

/* sections */
.stitle{left:0;width:1200px;text-align:center;font:700 33px "Montserrat",sans-serif;color:#333;letter-spacing:1px}
.intro{left:245px;width:710px;text-align:center;font-size:12px;line-height:22px;color:var(--muted)}
.card{top:879px;width:272px;height:349px;border:1px solid #e2e2e2;background:#fff}
.card .ph{width:100%;height:181px;background:linear-gradient(135deg,#c9ccd3,#8c95a3)}
.card .badge{position:absolute;left:110px;top:150px;width:52px;height:52px;border-radius:50%;background:var(--red);border:4px solid #fff;display:flex;align-items:center;justify-content:center}
.card h3{margin-top:40px;text-align:center;font-size:14px;font-weight:600;color:#333;letter-spacing:.5px}
.card p{margin:12px 20px 0;text-align:center;font-size:12px;line-height:22px;color:var(--muted)}
.arrow{width:32px;height:32px;background:var(--red);display:flex;align-items:center;justify-content:center;top:1017px}

.why{left:0;top:1292px;width:1200px;height:544px;background:var(--light)}
.why .kick{left:163px;top:106px;font:600 13px "Montserrat",sans-serif;color:#222}
.why h2{left:163px;top:136px;width:430px;font-size:27px;line-height:33px;font-weight:700;color:var(--navy)}
.why p{left:163px;width:420px;font-size:12.5px;line-height:22px;color:#333}
.why .more{left:163px;top:406px;width:122px;height:40px;background:var(--red);color:#fff;font:600 14px "Open Sans",sans-serif}
.video{left:615px;top:106px;width:418px;height:351px;background:linear-gradient(120deg,#2b2f36,#6b6a6d 55%,#3a3d45)}

.callback{left:0;top:1836px;width:599px;height:539px;background:var(--red);color:#fff}
.cbphoto{left:599px;top:1836px;width:601px;height:539px;background:linear-gradient(100deg,#f4f4f6,#e6dfdc 50%,#c9c3c4)}
.callback h2{left:156px;top:78px;font:500 40px "Raleway",sans-serif;color:#fff}
.callback h2 span{color:var(--navy)}
.callback p{left:156px;top:130px;width:400px;font-size:12.5px;line-height:21px}
.field{background:#fff;color:#888;font-size:12px;padding:9px 10px;height:34px}
.submit{left:158px;top:413px;width:119px;height:40px;background:var(--black);color:#fff;font:700 14px "Montserrat",sans-serif}

.post{top:2584px;width:271px}
.post .ph{height:166px;background:linear-gradient(135deg,#b7bdc8,#55607a)}
.post h4{margin-top:20px;font:600 14.5px "Montserrat",sans-serif;line-height:23px;color:#222}
.post p{margin-top:12px;font-size:12px;line-height:20px;color:var(--muted)}
.post a{display:block;margin-top:16px;font:700 12px "Montserrat",sans-serif;color:var(--red)}

.footer{left:0;top:3052px;width:1200px;height:390px;background:var(--dark);color:#d7d9de}
.brochure{left:161px;top:2995px;width:874px;height:103px;background:var(--red);color:#fff}
.brochure h3{left:22px;top:24px;font:700 21px "Montserrat",sans-serif}
.brochure p{left:22px;top:54px;width:600px;font-size:12px;line-height:17px}
.brochure .dl{left:720px;top:30px;width:146px;height:42px;background:var(--black);color:#fff;font:700 12px "Montserrat",sans-serif}
.fbrand{left:166px;top:105px;color:#fff;font:700 30px "Montserrat",sans-serif;letter-spacing:1px;display:flex;gap:10px;align-items:center}
.fbrand i{width:13px;height:13px;background:#fff}
.ftext{left:166px;top:160px;width:250px;font-size:12.5px;line-height:23px}
.fhead{font:600 18px "Montserrat",sans-serif;color:#fff}
.links{font-size:12.5px;line-height:22px}
.links li{list-style:none;padding-left:16px;position:relative}
.links li::before{content:"";position:absolute;left:0;top:9px;width:5px;height:5px;background:var(--red);border-radius:50%}
.cinfo{display:flex;gap:14px;font-size:12px;line-height:19px}
.cinfo .ic{width:36px;height:36px;flex:none;border:1px solid #8d909b;border-radius:50%;display:flex;align-items:center;justify-content:center}
.fline{left:161px;top:3385px;width:874px;height:1px;background:#595d6b}
.copy{left:161px;top:3400px;font-size:12px;color:#d7d9de}
.copy span{color:var(--red)}
.fsocial{left:865px;top:3394px;display:flex;gap:16px}
.fsocial span{width:26px;height:26px;border-radius:50%;background:#6a6e7c}
.fsocial span.on{background:#2a9fd6}
</style>
</head>
<body>

<section class="hero abs" role="img" aria-label="Photo of smiling business professionals in an office reviewing documents"></section>
<div class="topbar abs">
  <svg class="pin abs" width="10" height="14" viewBox="0 0 10 14"><path d="M5 0a5 5 0 0 0-5 5c0 4 5 9 5 9s5-5 5-9a5 5 0 0 0-5-5zm0 7a2 2 0 1 1 0-4 2 2 0 0 1 0 4z" fill="#ec1c24"/></svg>
  <span class="addr abs">4120 Marlow Avenue, Suite 210, Fenwick, CA 90410-2200, USA</span>
  <div class="social abs"><span></span><span></span><span></span><span class="on"></span></div>
  <span class="lang abs">En ⌄</span>
</div>

<header class="header abs">
  <div class="brand abs"><i></i>PLOVTRIX</div>
  <div class="hcontact abs" style="left:330px;top:22px">
    <div class="ic"><svg width="18" height="18" viewBox="0 0 24 24"><path d="M6.6 10.8a15 15 0 0 0 6.6 6.6l2.2-2.2a1 1 0 0 1 1-.25 11 11 0 0 0 3.6.6 1 1 0 0 1 1 1V20a1 1 0 0 1-1 1A17 17 0 0 1 3 4a1 1 0 0 1 1-1h3.5a1 1 0 0 1 1 1 11 11 0 0 0 .6 3.6 1 1 0 0 1-.25 1z" fill="#ec1c24"/></svg></div>
    <div><b>Call Us Now</b>+1 (555) 014-2290</div>
  </div>
  <div class="hcontact abs" style="left:503px;top:22px">
    <div class="ic"><svg width="18" height="18" viewBox="0 0 24 24"><rect x="3" y="5" width="18" height="14" rx="1" fill="none" stroke="#ec1c24" stroke-width="2"/><path d="M3 6l9 7 9-7" fill="none" stroke="#ec1c24" stroke-width="2"/></svg></div>
    <div><b>Send Mail Us</b>contactus@plovtrix.com</div>
  </div>
  <div class="consult abs">CONSULTATION</div>
</header>

<nav class="nav abs">
  <span class="home"><svg width="16" height="16" viewBox="0 0 24 24"><path d="M12 3l9 8h-3v9h-5v-6h-2v6H6v-9H3z" fill="#fff"/></svg></span>
  <a>ABOUT</a><a>RECRUITMENT</a><a>CONSULTING</a><a>DEVELOPMENT</a><a>COACHING</a><a>EVENTS</a><a>BLOG</a><a>CONTACT</a>
  <svg style="position:absolute;right:14px" width="14" height="14" viewBox="0 0 24 24"><circle cx="10" cy="10" r="7" fill="none" stroke="#ec1c24" stroke-width="2.5"/><path d="M15 15l6 6" stroke="#ec1c24" stroke-width="2.5"/></svg>
</nav>

<h1 class="abs" style="left:0;top:350px;width:1200px;text-align:center;color:#fff;font-size:37px;font-weight:600;text-shadow:0 2px 6px rgba(0,0,0,.4)">Better Data, Better Target,Better Results</h1>
<p class="abs" style="left:300px;top:417px;width:600px;text-align:center;color:#fff;font-size:14px;line-height:26px">Universal business theme continues to grow &nbsp;continues to grow ever day thanks to<br>the confidence our clients have in US.</p>
<div class="btn b1 abs">OUR COMPANY</div>
<div class="btn b2 abs">CONTACT US</div>

<h2 class="stitle abs" style="top:740px">OUR FEATURED SERVICES</h2>
<p class="intro abs" style="top:808px">Lorem ipsum dolor sit amet, lorem nibh lectus urna arcu, lorem erat semper, auctor suspendisse quisque mo-lestie ut. Elit massa dui, leo enim magna. Cursus maecenas cubilia, ac nonummy, egestas mauris.</p>

<div class="arrow abs" style="left:121px"><svg width="10" height="10" viewBox="0 0 10 10"><path d="M7 1L3 5l4 4" stroke="#fff" stroke-width="2" fill="none"/></svg></div>
<div class="arrow abs" style="left:1043px"><svg width="10" height="10" viewBox="0 0 10 10"><path d="M3 1l4 4-4 4" stroke="#fff" stroke-width="2" fill="none"/></svg></div>

<article class="card abs" style="left:168px">
  <div class="ph" role="img" aria-label="Photo of a business team meeting around a laptop"></div>
  <div class="badge"><svg width="22" height="22" viewBox="0 0 24 24"><ellipse cx="12" cy="5" rx="8" ry="3" fill="#fff"/><path d="M4 5v14c0 1.7 3.6 3 8 3s8-1.3 8-3V5" fill="none" stroke="#fff" stroke-width="2"/><path d="M4 12c0 1.7 3.6 3 8 3s8-1.3 8-3" fill="none" stroke="#fff" stroke-width="2"/></svg></div>
  <h3>B2B DATABASE</h3>
  <p>Recruing experienced change &amp; trans-formation professionals for short/long term or permanent roles.</p>
</article>
<article class="card abs" style="left:459px">
  <div class="ph" role="img" aria-label="Photo of colleagues working together at a desk"></div>
  <div class="badge"><svg width="22" height="22" viewBox="0 0 24 24"><circle cx="12" cy="12" r="9" fill="none" stroke="#fff" stroke-width="2"/><circle cx="12" cy="12" r="5" fill="none" stroke="#fff" stroke-width="2"/><circle cx="12" cy="12" r="1.8" fill="#fff"/></svg></div>
  <h3>TARGET MARKETING</h3>
  <p>We support clients delivering the strate-gies &amp; capabilities that underpin suc-cessful, measurable change.</p>
</article>
<article class="card abs" style="left:753px">
  <div class="ph" role="img" aria-label="Photo of business people in suits talking"></div>
  <div class="badge"><svg width="22" height="22" viewBox="0 0 24 24"><path d="M4 13a8 8 0 0 1 16 0" fill="none" stroke="#fff" stroke-width="2"/><rect x="3" y="12" width="4" height="6" rx="1" fill="#fff"/><rect x="17" y="12" width="4" height="6" rx="1" fill="#fff"/></svg></div>
  <h3>CALL CENTRE</h3>
  <p>Helping your organisation achieve the right culture, capabilities &amp; planning to facilitate development.</p>
</article>

<section class="why abs">
  <div class="kick abs">Why We Are The Best</div>
  <h2 class="abs">We have 25 years experiens &amp; We provied best solution for grow your bussines</h2>
  <p class="abs" style="top:240px">Lorem ipsum dolor sit amet, justo nunc orci donec sagittis metus dapi-bus, erat ullamcorper odio augue eleifend. consequat enim ullamcorp-er magnis dignissim nec phasellus. Lorem ipsum dolor sit amet, justo nunc orci donec sagittis metus dapibus, erat ullamcorper odio augue eleifend. consequat enim</p>
  <p class="abs" style="top:350px">Lorem ipsum dolor sit amet, justo nunc orci donec sagittis metus dapi-bus, erat ullamcorper odio augue eleifend. consequat enim .</p>
  <div class="btn more abs">Read More</div>
  <div class="video abs" role="img" aria-label="Video still of colleagues focused on a laptop"></div>
  <svg class="abs" style="left:800px;top:258px" width="48" height="48" viewBox="0 0 48 48"><circle cx="24" cy="24" r="22" fill="none" stroke="#fff" stroke-width="2"/><path d="M19 15l14 9-14 9z" fill="#fff"/></svg>
</section>

<section class="callback abs">
  <h2 class="abs"><span>Request</span> Callback</h2>
  <p class="abs">Lorem ipsum dolor sit amet, justo nunc orci donec sagittis metus dapi-bus, erat ullamcorper odio augue eleifend. consequat enim ullamcorp-er magnis dignissim nec phasellus</p>
  <div class="field abs" style="left:156px;top:215px;width:184px">Name</div>
  <div class="field abs" style="left:355px;top:215px;width:188px">Email</div>
  <div class="field abs" style="left:156px;top:263px;width:387px">Phone Number</div>
  <div class="field abs" style="left:156px;top:311px;width:387px;height:73px">I would like to discuss…</div>
  <div class="btn submit abs">SUBMIT</div>
</section>
<div class="cbphoto abs" role="img" aria-label="Photo of a smiling call centre agent wearing a headset"></div>

<h2 class="stitle abs" style="top:2435px">OUR LATEST POST</h2>
<p class="intro abs" style="top:2502px">Lorem ipsum dolor sit amet, lorem nibh lectus urna arcu, lorem erat semper, auctor suspendisse quisque mo-lestie ut. Elit massa dui, leo enim magna. Cursus maecenas cubilia, ac nonummy, egestas mauris.</p>

<article class="post abs" style="left:161px">
  <div class="ph" role="img" aria-label="Photo of a business team at a meeting table"></div>
  <h4>Fusce Adipiscing At Sed Aliquam Pellentesque Eu, Etiam In Massa.</h4>
  <p>Lorem ipsum dolor sit amet, fusce adipiscing at sed aliquam pellentesque eu, etiam in massa. Sagittis urna tellus augue montes .</p>
  <a>Read More</a>
</article>
<article class="post abs" style="left:452px">
  <div class="ph" role="img" aria-label="Photo collage of colleagues in an office"></div>
  <h4>Join With Us For Improve Your Business Idea.Eu, Etiam In Massa.</h4>
  <p>Lorem ipsum dolor sit amet, fusce adipiscing at sed aliquam pellentesque eu, etiam in massa. Sagittis urna tellus augue montes .</p>
  <a>Read More</a>
</article>
<article class="post abs" style="left:746px">
  <div class="ph" role="img" aria-label="Photo of business people reviewing documents"></div>
  <h4>Open A New Idea For Growth Your Business .Sagittis Urna Tellus Augue</h4>
  <p>Lorem ipsum dolor sit amet, fusce adipiscing at sed aliquam pellentesque eu, etiam in massa. Sagittis urna tellus augue montes .</p>
  <a>Read More</a>
</article>

<footer class="footer abs">
  <div class="fbrand abs"><i></i>PLOVTRIX</div>
  <p class="ftext abs">Lorem ipsum dolor sit amet, lorem nibh lectus urna arcu, lorem erat semper, auctor suspendisse quisque molestie ut. Elit massa dui, leo enim magna. Cursus maecenas cubilia, ac nonummy, egestas mauris.</p>

  <h4 class="fhead abs" style="left:505px;top:108px">Useful Links</h4>
  <ul class="links abs" style="left:505px;top:150px"><li>About</li><li>Recruitment</li><li>Consulting</li><li>Development</li><li>coaching</li></ul>
  <ul class="links abs" style="left:640px;top:150px"><li>Events</li><li>Blog</li><li>Contact</li></ul>

  <h4 class="fhead abs" style="left:778px;top:108px">Contact Us</h4>
  <div class="cinfo abs" style="left:778px;top:154px">
    <span class="ic"><svg width="12" height="16" viewBox="0 0 10 14"><path d="M5 0a5 5 0 0 0-5 5c0 4 5 9 5 9s5-5 5-9a5 5 0 0 0-5-5zm0 7a2 2 0 1 1 0-4 2 2 0 0 1 0 4z" fill="#d7d9de"/></svg></span>
    <span>Level 4, Suite 12 88 Harbour Lane<br>Eastwharf, Victoria 3999</span>
  </div>
  <div class="cinfo abs" style="left:778px;top:218px">
    <span class="ic"><svg width="16" height="16" viewBox="0 0 24 24"><rect x="3" y="5" width="18" height="14" rx="1" fill="none" stroke="#d7d9de" stroke-width="2"/><path d="M3 6l9 7 9-7" fill="none" stroke="#d7d9de" stroke-width="2"/></svg></span>
    <span style="padding-top:8px">info@plovtrix-mail.com</span>
  </div>
  <div class="cinfo abs" style="left:778px;top:275px">
    <span class="ic"><svg width="16" height="16" viewBox="0 0 24 24"><path d="M6.6 10.8a15 15 0 0 0 6.6 6.6l2.2-2.2a1 1 0 0 1 1-.25 11 11 0 0 0 3.6.6 1 1 0 0 1 1 1V20a1 1 0 0 1-1 1A17 17 0 0 1 3 4a1 1 0 0 1 1-1h3.5a1 1 0 0 1 1 1 11 11 0 0 0 .6 3.6 1 1 0 0 1-.25 1z" fill="#d7d9de"/></svg></span>
    <span>+61 1300 555 010, +61 3 5550 1234<br>+61 (0) 400 555 019 (mob)</span>
  </div>
</footer>

<section class="brochure abs">
  <h3 class="abs">CORPORATE BROCHURE</h3>
  <p class="abs">Learn our leading target marketing and intelligent data management solutions to attain new customers for your niche products and services.</p>
  <div class="btn dl abs">DOWNLOAD NOW</div>
</section>

<div class="fline abs"></div>
<p class="copy abs">Copyright 2018 © <span>Plovtrix</span></p>
<div class="fsocial abs"><span class="on"></span><span></span><span></span><span></span></div>

</body>
</html>
```